One page flyer for nonprofit focused IT company

I need a one page flyer (one side of a single 8.5x11 page) with text and graphics. The company logo is already done, and it must appear on the flyer along with other icons and graphics. The final design will be printed on heavy weight glossy paper as a handout and also distributed as a PDF.

The text is provided in an attachment, if it needs to be shortened let me know.

Industry/Entity Type

Information Technology

Requirements
Must have
• some flare (colors, icons or images)
Should not have
• While we work for nonprofits, my company is a FOR PROFIT company.

```html
<!DOCTYPE html>
<html lang="en">
<head>
<meta charset="utf-8">
<title>Northgate Systems Corporation – 50 Years of Nonprofit IT Services</title>
<link rel="stylesheet" href="https://fonts.googleapis.com/css2?family=Montserrat:wght@300;800;900&family=Rubik:wght@500;600&family=Roboto:wght@400;700&display=swap">
<style>
  :root{
    --maroon:#8b1428;
    --ink:#2f2f2f;
    --white:#ffffff;
    --page:#ececec;
    --paper-edge:#f4f4f4;
  }
  *{margin:0;padding:0;box-sizing:border-box}
  html,body{width:1200px;height:2667px;overflow:hidden;background:var(--page)}
  .flyer{
    position:absolute;left:43px;top:612px;width:960px;height:1243px;
    transform:scale(1.16);transform-origin:0 0;
    background:linear-gradient(180deg,var(--white) 0%,var(--paper-edge) 60%,var(--white) 100%);
    overflow:hidden;
    font-family:"Roboto",Arial,sans-serif;color:var(--ink);
  }
  .brand{position:absolute;left:0;top:0;width:960px;height:126px}
  .brand__mark{position:absolute;left:464px;top:22px;width:32px;height:32px;background:var(--maroon)}
  .brand__name{
    position:absolute;left:0;width:960px;top:64px;text-align:center;
    font-family:"Rubik",Arial,sans-serif;font-weight:500;font-size:25px;letter-spacing:1px;color:var(--maroon);
  }
  .brand__rule{position:absolute;top:114px;height:4px;background:var(--maroon)}
  .brand__rule--left{left:0;width:360px}
  .brand__rule--right{left:600px;width:360px}

  .banner{
    position:absolute;left:0;top:126px;width:960px;height:299px;background:var(--maroon);
    color:var(--white);text-align:center;font-family:"Montserrat",Arial,sans-serif;
  }
  .banner__line{position:absolute;left:0;width:960px;line-height:1}
  .banner__line--years{top:34px;font-weight:900;font-size:94px;letter-spacing:1px}
  .banner__line--of{top:133px;font-weight:300;font-size:66px}
  .banner__line--it{top:198px;font-weight:900;font-size:80px}

  .column{position:absolute;top:455px}
  .column--left{left:60px;width:397px}
  .column--right{left:505px;width:387px}
  .feature{position:absolute;left:0;width:100%}
  .feature__title{
    display:flex;align-items:flex-start;gap:7px;
    font-family:"Rubik",Arial,sans-serif;font-weight:600;font-size:16.5px;line-height:18px;color:var(--maroon);
    margin-bottom:4px;
  }
  .feature__title svg{flex:none;margin-top:2px}
  .feature__body{font-size:15.3px;line-height:18.8px;text-align:justify}
  .feature__body strong{font-weight:700}

  .footer{position:absolute;left:0;top:1172px;width:960px;height:71px}
  .footer__rule{position:absolute;left:0;top:0;width:960px;height:4px;background:var(--maroon)}
  .footer__band{position:absolute;left:0;top:8px;width:960px;height:63px;background:var(--maroon)}
  .contact{
    position:absolute;top:27px;display:flex;align-items:center;gap:8px;
    font-family:"Rubik",Arial,sans-serif;font-weight:500;font-size:15.5px;color:var(--white);
  }
  .contact--phone{left:72px}
  .contact--email{left:335px}
  .contact--web{left:659px}
</style>
</head>
<body>
<main class="flyer">
  <header class="brand">
    <span class="brand__mark"></span>
    <div class="brand__name">NORTHGATE SYSTEMS</div>
    <span class="brand__rule brand__rule--left"></span>
    <span class="brand__rule brand__rule--right"></span>
  </header>

  <section class="banner">
    <div class="banner__line banner__line--years">50 YEARS</div>
    <div class="banner__line banner__line--of">OF NONPROFIT</div>
    <div class="banner__line banner__line--it">IT SERVICES</div>
  </section>

  <section class="column column--left">
    <article class="feature" style="top:0">
      <h2 class="feature__title"><svg width="14" height="14" viewBox="0 0 14 14"><rect x="1" y="2" width="10" height="10" fill="none" stroke="#444" stroke-width="1.3"/><path d="M3.5 6.5l2.5 2.5 6.5-7" fill="none" stroke="#444" stroke-width="1.5"/></svg><span>An Efficient and Elegant Approach to<br>IT Solution Implementations</span></h2>
      <p class="feature__body">Northgate Systems Corporation has been supporting the Information Systems needs of nonprofits for over 50 years. We continually strive to bring the latest technologies and best practices to nonprofits to drive down the cost of IT while implementing systems that drive revenue. Our Agile approach to IT management means that we deliver working systems to every one of our clients every two weeks.</p>
    </article>
    <article class="feature" style="top:206px">
      <h2 class="feature__title"><svg width="14" height="14" viewBox="0 0 14 14"><rect x="1" y="2" width="10" height="10" fill="none" stroke="#444" stroke-width="1.3"/><path d="M3.5 6.5l2.5 2.5 6.5-7" fill="none" stroke="#444" stroke-width="1.5"/></svg><span>Successes 90% Reduction in Software<br>Development Costs</span></h2>
      <p class="feature__body">Carver Ratings' National Vehicle Retailers Association needed to update their core product offering; they engaged their in-house IT department who estimated the project would take 3 years at a cost of $3,000,000. NVRA decided to work with Northgate Systems Corporation instead, and the product was released to production in only 9 months at <strong>one tenth of the cost</strong>, only $300,000</p>
    </article>
    <article class="feature" style="top:425px">
      <h2 class="feature__title"><svg width="14" height="14" viewBox="0 0 14 14"><rect x="1" y="2" width="10" height="10" fill="none" stroke="#444" stroke-width="1.3"/><path d="M3.5 6.5l2.5 2.5 6.5-7" fill="none" stroke="#444" stroke-width="1.5"/></svg><span>10x Increase in Membership</span></h2>
      <p class="feature__body" style="margin-top:8px">Greenways Path Conservancy needed to move to online membership registration and contracted with Northgate Systems Corporation to build a significant online presence and engage potential members. Through compelling online tools and mobile applications Greenways Path has <strong>increased membership 10 fold.</strong></p>
    </article>
    <article class="feature" style="top:601px">
      <h2 class="feature__title"><svg width="14" height="14" viewBox="0 0 14 14"><rect x="1" y="2" width="10" height="10" fill="none" stroke="#444" stroke-width="1.3"/><path d="M3.5 6.5l2.5 2.5 6.5-7" fill="none" stroke="#444" stroke-width="1.5"/></svg><span>Member Donor Database</span></h2>
      <p class="feature__body">Northgate Systems Corporation's GiveLedger Member / Donor CRM system is fully customized for each client meeting the unique needs of your organization.</p>
    </article>
  </section>

  <section class="column column--right">
    <article class="feature" style="top:0">
      <h2 class="feature__title"><svg width="14" height="14" viewBox="0 0 14 14"><rect x="1" y="2" width="10" height="10" fill="none" stroke="#444" stroke-width="1.3"/><path d="M3.5 6.5l2.5 2.5 6.5-7" fill="none" stroke="#444" stroke-width="1.5"/></svg><span>20% Reduction in Overhead</span></h2>
      <p class="feature__body" style="margin-top:8px">The National Council for Working Families had antiquated systems and processes in place to manage over 500 chapters across the nation. Working with NSC they implemented online tools to allow communication and management between the local chapters and national headquarters. This eliminated much of the overhead of chapter management, <strong>reducing HR costs by 20%.</strong></p>
    </article>
    <article class="feature" style="top:190px">
      <h2 class="feature__title"><svg width="14" height="14" viewBox="0 0 14 14"><rect x="1" y="2" width="10" height="10" fill="none" stroke="#444" stroke-width="1.3"/><path d="M3.5 6.5l2.5 2.5 6.5-7" fill="none" stroke="#444" stroke-width="1.5"/></svg><span>Mobile Applications</span></h2>
      <p class="feature__body" style="margin-top:8px">Northgate Systems Corporation implements mobile applications for phones and tablets to provide direct communications with members and donors enabling real-time, two way interaction.</p>
    </article>
    <article class="feature" style="top:318px">
      <h2 class="feature__title"><svg width="14" height="14" viewBox="0 0 14 14"><rect x="1" y="2" width="10" height="10" fill="none" stroke="#444" stroke-width="1.3"/><path d="M3.5 6.5l2.5 2.5 6.5-7" fill="none" stroke="#444" stroke-width="1.5"/></svg><span>Systems Integration</span></h2>
      <p class="feature__body" style="margin-top:8px">Every nonprofit's IT applications are scattered and disconnected. Northgate System Corporation has decades of experience integrating these applications into a single cohesive system.</p>
    </article>
    <article class="feature" style="top:444px">
      <h2 class="feature__title"><svg width="14" height="14" viewBox="0 0 14 14"><rect x="1" y="2" width="10" height="10" fill="none" stroke="#444" stroke-width="1.3"/><path d="M3.5 6.5l2.5 2.5 6.5-7" fill="none" stroke="#444" stroke-width="1.5"/></svg><span>Business Intelligence and Reporting</span></h2>
      <p class="feature__body" style="margin-top:8px">Northgate Systems Corporation can wrestle all of an organization's data into simple executive dashboards and reports.</p>
    </article>
    <article class="feature" style="top:552px">
      <h2 class="feature__title"><svg width="14" height="14" viewBox="0 0 14 14"><rect x="1" y="2" width="10" height="10" fill="none" stroke="#444" stroke-width="1.3"/><path d="M3.5 6.5l2.5 2.5 6.5-7" fill="none" stroke="#444" stroke-width="1.5"/></svg><span>Cloud Migration</span></h2>
      <p class="feature__body" style="margin-top:8px">Reduce IT costs by migrating to the latest cloud solutions.</p>
    </article>
  </section>

  <footer class="footer">
    <span class="footer__rule"></span>
    <div class="footer__band"></div>
    <div class="contact contact--phone">
      <svg width="20" height="20" viewBox="0 0 20 20"><circle cx="10" cy="10" r="9" fill="none" stroke="#fff" stroke-width="1.3"/><path d="M7 5.5l2 2-1 1.5c.6 1.3 1.7 2.4 3 3l1.5-1 2 2-1.3 1.5C9.8 14 6.2 10.4 5.5 6.8z" fill="#fff"/></svg>
      <span>555-018-2746</span>
    </div>
    <div class="contact contact--email">
      <svg width="20" height="20" viewBox="0 0 20 20"><circle cx="10" cy="10" r="9" fill="none" stroke="#fff" stroke-width="1.3"/><rect x="5.5" y="7" width="9" height="6.5" fill="#fff"/><path d="M5.5 7l4.5 3.6L14.5 7" fill="none" stroke="#8b1428" stroke-width="1"/></svg>
      <span>info@northgatesystems.com</span>
    </div>
    <div class="contact contact--web">
      <svg width="20" height="20" viewBox="0 0 20 20"><circle cx="10" cy="10" r="9" fill="none" stroke="#fff" stroke-width="1.3"/><circle cx="10" cy="10" r="5" fill="none" stroke="#fff" stroke-width="1"/><ellipse cx="10" cy="10" rx="2.2" ry="5" fill="none" stroke="#fff" stroke-width="1"/><path d="M5 10h10" stroke="#fff" stroke-width="1"/></svg>
      <span>www.northgatesystems.com</span>
    </div>
  </footer>
</main>
</body>
</html>
```